Marwick Biomedical Research Institute (MBRI) Web Design

MBRI is a non-profit organization focused on saving the lives of terminally ill patients by becoming the leaders in cutting-edge research, innovative technologies, utilizing national and international partnerships as well as the associated allopathic and naturopathic treatments necessary to do so.

Our primary focus is raising funds to support the research and acquisition of new technologies for life saving treatments which are NOT a one size fits all approach like conventional medicine but rather a marriage of the latest technologies used in combination with other new treatment possibilities for a successful end result.

Our domain is marwickbri.org

Logo files are attached.

Looking for something clean, light, healthy.

Target Market(s)

The site should look and feel towards research/scientific grant writing.
Medical professionals, Medical Scientists.

Industry/Entity Type

Medical And Science

Number of Pages Required

4 page

Requirements
Nice to have
• Here are examples of sites I like in the order of how much I like them.
• https://www.palvorn.org/give.html
• https://www.thekqtf.org/donate-to-kqtf
• https://www.veltrasound.org/we-are-vsf/join-the-cause
• https://www.orvenly.org/involved/donate.html
• https://give.zdkt.org/checkout/donation?eid=58217
• https://www.quimbrel.org/how-you-can-help
• https://donate3.orvenly.org/

```html
<!DOCTYPE html>
<html lang="en">
<head>
<meta charset="utf-8">
<title>Ways to Give – Marwick Biomedical Research Institute</title>
<link rel="stylesheet" href="https://fonts.googleapis.com/css2?family=Titillium+Web:wght@300;400;600&family=Open+Sans:wght@400;600;700&display=swap">
<style>
:root{
  --green:#4b9d3b;
  --green-dark:#3d8a2f;
  --blue:#1d6fb8;
  --ink:#222;
  --muted:#9a9a9a;
  --light:#f3f3f3;
  --footer:#353535;
  --white:#fff;
}
*{box-sizing:border-box;margin:0;padding:0}
html,body{width:1200px;height:3103px;overflow:hidden}
body{position:relative;background:var(--white);font-family:"Open Sans",Arial,sans-serif;color:var(--ink)}
.abs{position:absolute}
.heading{font-family:"Titillium Web",Arial,sans-serif;font-weight:300;letter-spacing:1px}
.btn{position:absolute;display:flex;align-items:center;justify-content:center;color:var(--white);font-size:11px;font-weight:700;text-transform:uppercase;background:var(--green);border-right:5px solid var(--blue)}
.btn.blue{background:var(--blue);border-right-color:var(--green)}

/* header */
.brand{left:199px;top:26px;display:flex;align-items:center;gap:12px}
.brand-dot{width:36px;height:36px;border-radius:50%;background:var(--green)}
.brand-name{font-family:"Open Sans",sans-serif;font-weight:600;color:var(--blue);font-size:15px;line-height:1}
.contact-mail{left:640px;top:20px;display:flex;gap:14px;align-items:center;font-size:11px}
.mail-circle{width:44px;height:44px;border-radius:50%;border:2px solid #ddd;display:flex;align-items:center;justify-content:center}

/* nav */
.nav{left:0;top:87px;width:1200px;height:45px;background:var(--green)}
.nav ul{list-style:none;display:flex;position:absolute;left:199px;top:0;height:45px}
.nav li{color:var(--white);font-size:11px;font-weight:600;text-transform:uppercase;padding:0 25px;display:flex;align-items:center}
.nav li.active{background:var(--blue)}

/* hero */
.hero{left:0;top:132px;width:1200px;height:478px;background:linear-gradient(90deg,#6d7a5c,#8c9475 45%,#5f6d52);}
.hero::after{content:"";position:absolute;inset:0;background:rgba(20,25,20,.38)}
.hero-text{left:0;width:1200px;text-align:center;color:var(--white);z-index:2}
.hero-title{top:270px;font-size:35px;line-height:46px}
.hero-copy{top:385px;font-size:14px;line-height:24px}
.hero-arrow{width:42px;height:42px;border-radius:50%;background:rgba(0,0,0,.45);display:flex;align-items:center;justify-content:center;z-index:2;top:347px}
.dots{left:582px;top:553px;display:flex;gap:4px;z-index:2}
.dots span{width:10px;height:10px;border:1px solid var(--white)}

/* sections */
.section-title{left:0;width:1200px;text-align:center;font-size:28px;color:var(--ink)}
.body-copy{font-size:11.5px;line-height:21px;text-align:center;color:#333}
.bar-title{left:199px;width:802px;height:54px;background:var(--light);border-right:5px solid var(--blue);padding-left:16px;display:flex;align-items:center;font-size:27px}

.card{width:242px;background:var(--white);box-shadow:0 2px 6px rgba(0,0,0,.18);text-align:center}
.card-photo{height:149px;display:block}
.card-title{font-size:11px;font-weight:700;text-transform:uppercase;margin-top:20px}
.card-rule{width:40px;height:3px;background:#8fc3e6;margin:10px auto 12px}
.card-copy{font-size:10.5px;line-height:19px;color:var(--muted);padding:0 20px}

/* contribution band */
.band{left:0;top:1390px;width:1200px;height:462px;background:linear-gradient(135deg,#4d4f51,#6f7274 50%,#46484a)}
.band::after{content:"";position:absolute;inset:0;background:rgba(30,32,34,.35)}
.band-item{width:200px;text-align:center;color:var(--white);z-index:2}
.band-circle{width:70px;height:70px;border-radius:50%;border:2px solid var(--white);margin:0 auto;display:flex;align-items:center;justify-content:center;background:rgba(0,0,0,.15)}
.band-label{font-size:12px;font-weight:700;margin-top:18px;text-transform:uppercase}
.band-copy{font-size:11px;line-height:20px;margin-top:2px}

/* interest cards */
.mini-card{width:242px;height:176px;background:var(--white);box-shadow:0 2px 6px rgba(0,0,0,.18);text-align:center;padding-top:78px}
.mini-photo{width:118px;height:118px;border-radius:50%;border:4px solid var(--white);box-shadow:0 1px 4px rgba(0,0,0,.25)}

/* donor */
.donor-panel{left:434px;top:2381px;width:567px;height:338px;background:var(--light);border:1px solid #e4e4e4}
.donor-photo{left:199px;top:2421px;width:329px;height:258px;background:linear-gradient(120deg,#cfd3d5,#a9b3b8 55%,#8b98a0);border:6px solid var(--white);box-shadow:0 1px 4px rgba(0,0,0,.2)}

/* newsletter */
.newsletter{left:0;top:2789px;width:1200px;height:97px;background:var(--green);color:var(--white)}
.email-field{left:646px;top:2822px;width:264px;height:36px;border:1px solid var(--white);font-size:11px;padding-left:14px;display:flex;align-items:center;color:var(--white)}
.submit{left:910px;top:2822px;width:90px;height:36px;background:var(--blue);color:var(--white);font-size:12px;font-weight:700;display:flex;align-items:center;justify-content:center}

/* footer */
.footer{left:0;top:2886px;width:1200px;height:217px;background:var(--footer);color:var(--white)}
.foot-head{font-size:12px;font-weight:700;text-transform:uppercase;color:var(--white)}
.foot-copy{font-size:11px;line-height:21px;color:#eee}
.social{display:flex;gap:6px}
.social span{width:24px;height:24px;background:var(--blue);border:1px solid var(--white)}
</style>
</head>
<body>

<!-- header -->
<div class="abs brand">
  <span class="brand-dot"></span>
  <div class="brand-name">Marwick Biomedical Research Institute</div>
</div>
<div class="abs contact-mail">
  <div class="mail-circle">
    <svg width="20" height="14" viewBox="0 0 20 14"><rect x="1" y="1" width="18" height="12" rx="1" fill="var(--blue)"/><path d="M1 1l9 7 9-7" fill="none" stroke="#fff" stroke-width="1.5"/></svg>
  </div>
  <div><div style="font-weight:700">EMAIL :</div><div style="color:#666">info@marwickbri.org</div></div>
</div>
<div class="btn blue" style="left:822px;top:24px;width:177px;height:38px;font-size:12px;gap:10px">Donate Now
  <svg width="22" height="18" viewBox="0 0 22 18"><path d="M11 17L2 8a5 5 0 017-7l2 2 2-2a5 5 0 017 7z" fill="#fff"/></svg>
</div>

<nav class="abs nav">
  <ul>
    <li class="active">About Us</li>
    <li>Care &amp; Treatment</li>
    <li>Research</li>
    <li>Training</li>
    <li>Get Involved</li>
    <li>Ways to Give</li>
  </ul>
</nav>

<!-- hero -->
<section class="abs hero" role="img" aria-label="Photo of a smiling caregiver with a patient in a wheelchair in a sunny park"></section>
<h1 class="abs heading hero-text hero-title">WAYS TO GIVE TO<br>MARWICK BIOMEDICAL RESEARCH INSTITUTE</h1>
<p class="abs hero-text hero-copy">Lorem Ipsum is simply dummy text of the printing and typesetting industry. Lorem<br>Ipsum has been the industry's standard dummy text</p>
<div class="btn" style="left:472px;top:472px;width:124px;height:36px;z-index:2">Donate Now</div>
<div class="btn blue" style="left:601px;top:472px;width:130px;height:36px;z-index:2">Give Monthly</div>
<div class="abs hero-arrow" style="left:85px"><svg width="16" height="12" viewBox="0 0 16 12"><path d="M15 6H2M6 1L1 6l5 5" fill="none" stroke="#fff" stroke-width="2"/></svg></div>
<div class="abs hero-arrow" style="left:1080px"><svg width="16" height="12" viewBox="0 0 16 12"><path d="M1 6h13M10 1l5 5-5 5" fill="none" stroke="#fff" stroke-width="2"/></svg></div>
<div class="abs dots"><span></span><span></span><span></span></div>

<!-- about -->
<h2 class="abs heading section-title" style="top:670px">
  <span style="color:var(--blue);font-size:17px;vertical-align:middle">■■</span> ABOUT US <span style="color:var(--blue);font-size:17px;vertical-align:middle">■■</span>
</h2>
<p class="abs body-copy" style="left:220px;top:720px;width:760px">Lorem Ipsum is simply dummy text of the printing and typesetting industry. Lorem Ipsum has been the industry's standard dummy text ever since the 1500s, when an unknown printer took a galley of type and scrambled it to make a type specimen book. It has survived not only five centuries, but also the leap into ipsum...</p>
<div class="btn" style="left:537px;top:815px;width:130px;height:36px">Donate Now</div>

<!-- ways to give -->
<h2 class="abs heading bar-title" style="top:923px">THERE ARE MANY WAYS TO GIVE TO MBRI</h2>

<article class="abs card" style="left:199px;top:1024px;height:273px">
  <div class="card-photo" role="img" aria-label="Photo of volunteers packing donation boxes" style="background:linear-gradient(120deg,#8a7a66,#b59c7e 50%,#6f7d8a)"></div>
  <div class="card-title">Memorials &amp; Dedications</div><div class="card-rule"></div>
  <p class="card-copy">Lorem Ipsum is simply dummy text of the printing and typesetting...</p>
</article>
<article class="abs card" style="left:479px;top:1024px;height:273px">
  <div class="card-photo" role="img" aria-label="Photo of friends talking together on a sofa" style="background:linear-gradient(120deg,#7d8f9c,#b9a893 50%,#8da0b0)"></div>
  <div class="card-title">Legacy and Planned Giving</div><div class="card-rule"></div>
  <p class="card-copy">Lorem Ipsum is simply dummy text of the printing and typesetting...</p>
</article>
<article class="abs card" style="left:759px;top:1024px;height:273px">
  <div class="card-photo" role="img" aria-label="Photo of coworkers sorting donated goods" style="background:linear-gradient(120deg,#a9b4bb,#8c8f94 50%,#6b8f58)"></div>
  <div class="card-title">Give at Work</div><div class="card-rule"></div>
  <p class="card-copy">Lorem Ipsum is simply dummy text of the printing and typesetting...</p>
</article>
<div class="btn" style="left:265px;top:1283px;width:110px;height:28px">Read More</div>
<div class="btn" style="left:545px;top:1283px;width:110px;height:28px">Read More</div>
<div class="btn" style="left:825px;top:1283px;width:110px;height:28px">Read More</div>

<!-- contribution band -->
<section class="abs band" role="img" aria-label="Photo of volunteers joining hands in a circle, seen from below"></section>
<svg class="abs" style="left:576px;top:1460px;z-index:2" width="48" height="44" viewBox="0 0 48 44"><path d="M24 42L5 22A11 11 0 0124 8a11 11 0 0119 14z" fill="none" stroke="#fff" stroke-width="3"/><path d="M14 24l8-6 6 5 6-4" fill="none" stroke="#fff" stroke-width="3"/></svg>
<h2 class="abs heading section-title" style="top:1515px;color:#fff;font-size:27px;z-index:2">YOUR CONTRIBUTION EXTENDS LIVES.</h2>
<div class="abs" style="left:304px;top:1645px;width:586px;height:2px;background:#fff;z-index:2"></div>

<div class="abs band-item" style="left:169px;top:1610px">
  <div class="band-circle"><svg width="30" height="30" viewBox="0 0 30 30"><rect x="6" y="3" width="16" height="22" rx="2" fill="none" stroke="#fff" stroke-width="2"/><path d="M14 16l4 4 7-8" fill="none" stroke="#fff" stroke-width="2"/></svg></div>
  <div class="band-label">Give Online</div><p class="band-copy">Lorem Ipsum is sipldummy<br>text of the printing</p>
</div>
<div class="abs band-item" style="left:392px;top:1610px">
  <div class="band-circle"><svg width="30" height="24" viewBox="0 0 30 24"><rect x="2" y="3" width="26" height="18" fill="none" stroke="#fff" stroke-width="2"/><path d="M2 3l13 10L28 3" fill="none" stroke="#fff" stroke-width="2"/></svg></div>
  <div class="band-label">Give by Mail</div><p class="band-copy">Lorem Ipsum is sipldummy<br>text of the printing</p>
</div>
<div class="abs band-item" style="left:606px;top:1610px">
  <div class="band-circle"><svg width="28" height="28" viewBox="0 0 28 28"><path d="M7 3l4 6-3 3c2 4 4 6 8 8l3-3 6 4-3 4C12 25 3 16 3 6z" fill="none" stroke="#fff" stroke-width="2"/></svg></div>
  <div class="band-label">Give by Online</div><p class="band-copy">Lorem Ipsum is sipldummy<br>text of the printing</p>
</div>
<div class="abs band-item" style="left:825px;top:1610px">
  <div class="band-circle"><svg width="30" height="30" viewBox="0 0 30 30"><path d="M15 16l-6-6a4 4 0 016-5 4 4 0 016 5z" fill="none" stroke="#fff" stroke-width="2"/><path d="M3 20c4 0 6 3 12 3s9-3 12-5" fill="none" stroke="#fff" stroke-width="2"/></svg></div>
  <div class="band-label">Donation FAQs</div><p class="band-copy">Lorem Ipsum is sipldummy<br>text of the printing</p>
</div>

<!-- also interested -->
<h2 class="abs heading bar-title" style="top:1926px">YOU MAY ALSO BE INTERESTED IN
  <svg style="position:absolute;right:18px;top:22px" width="34" height="12" viewBox="0 0 34 12"><path d="M14 6H2M6 2L2 6l4 4M20 6h12M28 2l4 4-4 4" fill="none" stroke="#333" stroke-width="1.5"/></svg>
</h2>

<article class="abs mini-card" style="left:199px;top:2098px">
  <div class="card-title">Why Support MBRI?</div>
  <p class="card-copy" style="margin-top:8px">Lorem Ipsum is simply dummy text of the printing and typesetting...</p>
</article>
<div class="abs mini-photo" role="img" aria-label="Donate now photo" style="left:261px;top:2033px;background:linear-gradient(135deg,#a0656a,#4d5a6d);display:flex;align-items:center;justify-content:center;color:#fff;font-size:10px;font-weight:700">DONATE NOW</div>

<article class="abs mini-card" style="left:479px;top:2098px">
  <div class="card-title">Meet Our Patients</div>
  <p class="card-copy" style="margin-top:8px">Lorem Ipsum is simply dummy text of the printing and typesetting...</p>
</article>
<div class="abs mini-photo" role="img" aria-label="Photo of a patient with her daughter" style="left:541px;top:2033px;background:linear-gradient(135deg,#e2d2c2,#b99b86)"></div>

<article class="abs mini-card" style="left:759px;top:2098px">
  <div class="card-title">Get Involved with MBRI</div>
  <p class="card-copy" style="margin-top:8px">Lorem Ipsum is simply dummy text of the printing and typesetting...</p>
</article>
<div class="abs mini-photo" role="img" aria-label="Photo of a smiling volunteer outdoors" style="left:821px;top:2033px;background:linear-gradient(135deg,#8fa678,#9d9fa2)"></div>

<div class="abs" style="left:0;top:2315px;width:1200px;height:1px;background:#e6e6e6"></div>

<!-- monthly donor -->
<div class="abs donor-panel"></div>
<div class="abs donor-photo" role="img" aria-label="Photo of a smiling senior woman in a clinic"></div>
<svg class="abs" style="left:747px;top:2428px" width="40" height="40" viewBox="0 0 40 40"><path d="M20 22l-8-8a5 5 0 018-6 5 5 0 018 6z" fill="var(--blue)"/><path d="M4 18c2 8 8 14 16 18 8-4 14-10 16-18" fill="none" stroke="var(--blue)" stroke-width="3"/></svg>
<h2 class="abs heading" style="left:528px;top:2477px;width:473px;text-align:center;font-size:28px;color:#777">BECOME A MONTHLY DONOR</h2>
<p class="abs body-copy" style="left:560px;top:2526px;width:410px;color:var(--muted)">Lorem Ipsum is simply dummy text of the printing and typesetting industry. Lorem Ipsum has been the industry's standard dummy text ever since the 1500s, when an unknown printer took a galley of type and scrambled it to make a type specimen book.</p>
<div class="btn" style="left:674px;top:2638px;width:187px;height:34px">Become a Monthly Donor</div>

<!-- newsletter -->
<section class="abs newsletter">
  <svg class="abs" style="left:84px;top:18px" width="64" height="62" viewBox="0 0 64 62"><path d="M4 24L32 4l28 20v36H4z" fill="#fff"/><rect x="14" y="14" width="36" height="26" fill="var(--green)"/><path d="M20 22h24M20 30h24" stroke="#fff" stroke-width="3"/><path d="M4 24l28 20 28-20" fill="none" stroke="var(--green)" stroke-width="3"/></svg>
  <div class="abs heading" style="left:199px;top:22px;font-size:23px;font-weight:400">GET IN TOUCH WITH MBRI</div>
  <div class="abs" style="left:199px;top:56px;font-size:11.5px">Submit your email and stay in touch by notify our news &amp; update regularly</div>
</section>
<div class="abs email-field">Enter Your Email</div>
<div class="abs submit">SUBMIT</div>

<!-- footer -->
<footer class="abs footer">
  <div class="abs foot-head" style="left:199px;top:51px">MBRI Information</div>
  <p class="abs foot-copy" style="left:199px;top:88px;width:300px">Lorem Ipsum is simply dummy text of the printing and typesetting industry. Lorem Ipsum has been the industry's standard dummy text ever since the 1500s, when an unknown printer took ...</p>
  <div class="abs" style="left:199px;top:184px;font-size:11px;color:var(--blue)">READ MORE →</div>

  <div class="abs foot-head" style="left:543px;top:51px">Contact Us</div>
  <svg class="abs" style="left:543px;top:94px" width="14" height="14" viewBox="0 0 28 28"><path d="M7 3l4 6-3 3c2 4 4 6 8 8l3-3 6 4-3 4C12 25 3 16 3 6z" fill="var(--blue)"/></svg>
  <div class="abs foot-copy" style="left:585px;top:90px">+1 555 014 2290</div>
  <svg class="abs" style="left:543px;top:130px" width="12" height="16" viewBox="0 0 12 16"><path d="M6 16S0 9 0 6a6 6 0 0112 0c0 3-6 10-6 10z" fill="var(--blue)"/><circle cx="6" cy="6" r="2" fill="var(--footer)"/></svg>
  <div class="abs foot-copy" style="left:585px;top:122px;line-height:18px">Lorem Ipsum is simply<br>of the printing</div>
  <svg class="abs" style="left:543px;top:180px" width="16" height="12" viewBox="0 0 16 12"><rect width="16" height="12" fill="var(--blue)"/><path d="M0 0l8 6 8-6" fill="none" stroke="var(--footer)" stroke-width="1.5"/></svg>
  <div class="abs foot-copy" style="left:585px;top:174px">info@marwickbri.org</div>

  <div class="abs foot-head" style="left:880px;top:51px">Follow Us</div>
  <div class="abs social" style="left:880px;top:94px"><span></span><span></span><span></span><span></span></div>
  <div class="abs foot-copy" style="left:766px;top:140px;width:234px;text-align:right">© Copyright 2017 MBRI. All Rights Reserved.<br>Privacy Policy</div>
</footer>

</body>
</html>
```